New LLC consulting company needs a business card design

I need a business card design for new company in Alexandria Virginia called TK Verdane Consulting LLC. The company is focused on consulting for defense and national security issues with expertise in nuclear and space topics. I would like to see designs that are simple and I am open to colors except for brown.

Target Market(s)

All businesses that are seeking consulting help

Industry/Entity Type

Consulting

Contact Information for Business Card

Name of company - TK Verdane Consulting LLC; name (Delia Pratt) President; email: prattdq47@mailvessa.com; Phone: 703-555-0142

Requirements
Must have
• The details described above
Nice to have
• I'm open to all ideas
Should not have
• No brown

```html
<!DOCTYPE html>
<html lang="en">
<head>
<meta charset="utf-8">
<title>Delia Pratt — TK Verdane Consulting LLC</title>
<link rel="stylesheet" href="https://fonts.googleapis.com/css2?family=Montserrat:wght@400;700&display=swap">
<style>
  :root {
    --backdrop: #1f3a5f;
    --card: #ffffff;
    --accent: #1f3a5f;
    --ink: #2b2b2b;
  }
  html, body {
    margin: 0;
    padding: 0;
    width: 1200px;
    height: 1059px;
    overflow: hidden;
    background: var(--backdrop);
  }
  .business-card {
    position: absolute;
    left: 384px;
    top: 152px;
    width: 432px;
    height: 756px;
    background: var(--card);
    border-radius: 38px;
    box-shadow: 0 0 30px rgba(10, 20, 40, 0.45);
    display: flex;
    flex-direction: column;
    align-items: center;
    justify-content: center;
    font-family: "Montserrat", sans-serif;
    text-align: center;
  }
  .company-name {
    position: absolute;
    top: 72px;
    left: 0;
    right: 0;
    margin: 0;
    color: var(--accent);
    font-weight: 700;
    font-size: 18px;
    letter-spacing: 1.5px;
    text-transform: uppercase;
  }
  .card-name {
    margin: 0;
    color: var(--accent);
    font-weight: 700;
    font-size: 34px;
    line-height: 1;
    letter-spacing: 0.2px;
  }
  .card-title {
    margin: 14px 0 0;
    color: var(--ink);
    font-weight: 400;
    font-size: 20px;
    letter-spacing: 0.5px;
  }
  .contact-divider {
    margin-top: 16px;
    display: flex;
    align-items: center;
    gap: 11px;
  }
  .contact-divider .rule {
    display: block;
    width: 62px;
    height: 4px;
  }
  .contact-divider .icon {
    display: block;
    width: 30px;
    height: 30px;
  }
  .contact-list {
    margin: 16px 0 0;
    padding: 0;
    list-style: none;
    color: var(--ink);
    font-size: 19px;
    letter-spacing: 0.4px;
    line-height: 35px;
  }
</style>
</head>
<body>
  <section class="business-card">
    <p class="company-name">TK Verdane Consulting LLC</p>
    <h1 class="card-name">Delia Pratt</h1>
    <p class="card-title">President</p>
    <div class="contact-divider">
      <svg class="rule" viewBox="0 0 62 4" aria-hidden="true">
        <path d="M0 2 Q31 0.2 62 0.8 L62 3.2 Q31 3.8 0 2 Z" fill="var(--accent)"/>
      </svg>
      <svg class="icon" viewBox="0 0 30 30" aria-hidden="true">
        <circle cx="15" cy="15" r="15" fill="var(--accent)"/>
        <rect x="6" y="9.5" width="18" height="11" rx="1" fill="#fff"/>
        <path d="M6.5 10 L15 16.5 L23.5 10 M6.5 20 L12.5 15 M23.5 20 L17.5 15" stroke="var(--accent)" stroke-width="1.3" fill="none"/>
      </svg>
      <svg class="icon" viewBox="0 0 30 30" aria-hidden="true">
        <circle cx="15" cy="15" r="15" fill="var(--accent)"/>
        <path d="M9 8.5 L11.5 7.5 L13.5 11.5 L12 13 Q13.5 16.5 17 18 L18.5 16.5 L22.5 18.5 L21.5 21 Q19.5 23 16 21 Q10.5 18 8.5 13 Q7.5 10 9 8.5 Z" fill="#fff"/>
        <path d="M16 9.5 A5 5 0 0 1 20.5 14 M16.5 6.5 A8 8 0 0 1 23.5 13.5" stroke="#fff" stroke-width="1.4" fill="none" stroke-linecap="round"/>
      </svg>
      <svg class="rule" viewBox="0 0 62 4" aria-hidden="true">
        <path d="M62 2 Q31 0.2 0 0.8 L0 3.2 Q31 3.8 62 2 Z" fill="var(--accent)"/>
      </svg>
    </div>
    <ul class="contact-list">
      <li class="contact-email">prattdq47@mailvessa.com</li>
      <li class="contact-phone">703-555-0142</li>
    </ul>
  </section>
</body>
</html>
```